I have a business that exists already (Linden Conservatory of Music) that we offer music lessons to all instruments. I recently opened a smaller version called CHORDS by Linden that will only teach piano lessons. What I'm looking for now is a 3 page Website on word press. After I choose the design I like I want to be able to take over the website and bring it to our hosting company. We want full control of it and our team will take over. The reason I'm doing this is to have other visions and ideas from others. The first page will be about the company and our message/vision. Second page about the piano lessons. The third will be about franchising this concept "Chords by Linden" Attached are 3 Logos . Please refer to our existing website www.lindenmusicconservatory.example to look at our piano page and franchising page. Please feel free to message me if you need more info. Thanks
Please note I do not want the new website (Chords by Linden) To look like the other Website (Linden Conservatory of Music) Fresh new look. I do not want the colours red or using the Red logo. I only provided it so that you have an Idea of What the other business looks like and that you can take the piano content and franchise content off of it. Chords by Linden is smaller concept and only piano lessons.
Thanks
Only Piano lessons for all students
3 page

```html
<!DOCTYPE html>
<html lang="en">
<head>
<meta charset="utf-8">
<title>Chords by Linden — Piano Lessons For All Students</title>
<link href="https://fonts.googleapis.com/css2?family=Gelasio:ital,wght@0,400;0,500;1,400&family=Mulish:wght@400;600;700&family=Dancing+Script:wght@500&display=swap" rel="stylesheet">
<style>
:root{
  --black:#000000;
  --white:#ffffff;
  --orange:#f08a2c;
  --grey-band:#f4f3f2;
  --keys-band:#e2e2e2;
  --ink:#1b1b1b;
  --soft-peach:#fdf4ee;
  --quote-mark:#f6cfb0;
  --rule:#cfcfcf;
  --footer-text:#e6e6e6;
}
*{margin:0;padding:0;box-sizing:border-box}
html,body{width:1200px;height:3544px;overflow:hidden}
body{position:relative;background:var(--white);font-family:"Mulish",sans-serif;color:var(--ink)}
.abs{position:absolute}
.serif{font-family:"Gelasio",serif}
.btn{position:absolute;display:flex;align-items:center;justify-content:center;background:var(--orange);color:var(--white);border-radius:20px;font-family:"Dancing Script",cursive;font-size:18px;text-decoration:none}

/* hero */
.hero{position:absolute;left:0;top:0;width:1200px;height:983px;background:var(--black)}
.hero-photo{position:absolute;left:0;top:0;width:757px;height:555px;background:linear-gradient(120deg,#2a2a2a 0%,#8d8d8d 35%,#cfcfcf 50%,#3b3b3b 75%,#000 100%)}
.logo{position:absolute;display:flex;align-items:center;gap:8px;font-family:"Gelasio",serif;color:var(--white);font-size:30px;letter-spacing:1px;white-space:nowrap}
.logo-dot{width:12px;height:12px;border-radius:50%;background:var(--white);flex:none}
.nav{position:absolute;top:48px;left:593px;font-family:"Gelasio",serif;font-size:14px}
.nav a{position:absolute;top:0;white-space:nowrap;color:var(--white);text-decoration:none}
.nav a.current{color:var(--orange)}
.hero-kicker{left:775px;top:218px;color:var(--white);font-size:22px}
.hero-title{left:773px;top:243px;color:var(--orange);font-size:48px;line-height:1.1;font-weight:400}
.hero-sub{left:775px;top:298px;color:var(--white);font-size:33px}

.intro-title{left:145px;top:606px;color:var(--white);font-size:31px;letter-spacing:.5px;font-weight:400}
.intro-copy{left:145px;top:660px;width:482px;color:var(--white);font-size:12.6px;line-height:21.6px;letter-spacing:.2px}
.intro-copy p+p{margin-top:7px}
.photo-girl{left:663px;top:495px;width:395px;height:541px;background:linear-gradient(160deg,#5a4a3a 0%,#b8864e 40%,#7a5a3a 70%,#2a2a2a 100%)}

/* vision */
.photo-back{left:0;top:1037px;width:325px;height:287px;background:linear-gradient(130deg,#6a5a50 0%,#3a3230 60%,#2b2522 100%)}
.photo-front{left:106px;top:1137px;width:428px;height:408px;background:linear-gradient(135deg,#e9ecef 0%,#c9d2dc 40%,#8d9bb0 70%,#f2f2f2 100%)}
.section-title{font-size:31px;color:var(--ink);letter-spacing:.5px;font-weight:400}
.vision-title{left:578px;top:1192px}
.vision-copy{left:578px;top:1248px;width:482px;font-size:12.6px;line-height:21.6px;color:var(--ink)}
.vision-copy p+p{margin-top:7px}

/* programs */
.programs-band{left:0;top:1633px;width:1200px;height:870px;background:var(--grey-band)}
.programs-title{left:142px;top:1793px}
.programs-sub{left:143px;top:1836px;font-family:"Gelasio",serif;font-size:20px;line-height:27px;color:var(--ink)}
.accent-right{left:897px;top:1719px;width:161px;height:315px;background:var(--orange)}
.photo-pianist{left:575px;top:1739px;width:462px;height:342px;background:linear-gradient(100deg,#8a7d72 0%,#4a4440 40%,#1c1a19 75%,#3a332e 100%)}
.accent-left{left:142px;top:2027px;width:161px;height:315px;background:var(--orange)}
.photo-hands{left:162px;top:1980px;width:284px;height:341px;background:linear-gradient(200deg,#fff4e4 0%,#f1c99a 40%,#b88766 75%,#5b4a44 100%)}
.programs-list{left:603px;top:2124px;width:440px;list-style:none;font-size:13.6px;line-height:19.5px;color:var(--ink)}
.programs-list li+li{margin-top:11px}
.keys-band{left:0;top:2497px;width:1200px;height:117px;background:linear-gradient(180deg,var(--keys-band) 0%,#ececec 100%)}

/* testimonial */
.quote-mark{font-family:"Gelasio",serif;font-size:96px;color:var(--quote-mark);line-height:1}
.quote-open{left:244px;top:2686px}
.quote-close{left:880px;top:2750px}
.quote-text{left:0;top:2730px;width:1200px;text-align:center;font-family:"Gelasio",serif;font-style:italic;font-size:19px;color:var(--ink)}
.quote-rule{left:435px;top:2807px;width:329px;height:1px;background:var(--rule)}
.quote-notch{left:592px;top:2807px;width:0;height:0;border-left:7px solid transparent;border-right:7px solid transparent;border-top:7px solid var(--rule)}
.quote-name{left:0;top:2830px;width:1200px;text-align:center;font-family:"Gelasio",serif;font-size:17px;color:var(--ink)}
.stars{left:563px;top:2855px}

/* franchise */
.franchise{left:263px;top:2956px;width:680px;height:214px;background:var(--soft-peach);text-align:center}
.franchise h2{position:absolute;left:0;top:45px;width:100%;font-family:"Gelasio",serif;font-weight:400;font-size:33px;color:var(--ink)}
.franchise p{position:absolute;left:0;top:96px;width:100%;font-size:18px;color:#333}

/* footer */
.footer{left:0;top:3256px;width:1200px;height:250px;background:var(--black);color:var(--footer-text)}
.foot-head{position:absolute;top:57px;font-family:"Gelasio",serif;font-size:12.5px;color:var(--white);letter-spacing:.3px}
.quick-links{position:absolute;left:143px;top:83px;list-style:none;font-size:12.6px;line-height:26px}
.quick-links li::before{content:"»";margin-right:9px}
.contact{position:absolute;left:337px;top:84px;font-size:12.3px;line-height:17px;width:200px}
.contact .row{display:flex;gap:8px;margin-bottom:14px}
.contact svg{flex:none;margin-top:2px}
.map{position:absolute;left:623px;top:79px;width:208px;height:123px;border:3px solid #bfbfbf;background:linear-gradient(140deg,#a9cbe9 0%,#d3e3f1 45%,#e8e6dc 60%,#d9d4c5 100%)}
.foot-logo{left:894px;top:96px;font-size:24px;letter-spacing:.5px}
.socials{position:absolute;left:930px;top:169px;display:flex;gap:9px}
.socials span{width:22px;height:22px;border-radius:50%;border:1.5px solid var(--white)}
.copyright{left:0;top:3506px;width:1200px;height:38px;background:var(--orange);color:var(--white);font-size:11.5px;display:flex;align-items:center;justify-content:center}
.copyright b{margin:0 4px;font-weight:700}
</style>
</head>
<body>

<section class="hero" aria-label="Hero">
  <div class="hero-photo" role="img" aria-label="Close-up photograph of grand piano keys in black and white"></div>
</section>

<div class="logo" style="left:145px;top:30px"><span class="logo-dot"></span>CHORDS by Linden</div>

<nav class="nav">
  <a class="current" href="#" style="left:0">HOME</a>
  <a href="#" style="left:83px">PIANO LESSONS</a>
  <a href="#" style="left:233px">FRANCHISING</a>
  <a href="#" style="left:370px">CONTACT US</a>
</nav>

<div class="abs hero-kicker">We Will Provide</div>
<h1 class="abs serif hero-title">Piano Lessons</h1>
<div class="abs serif hero-sub">For All Students</div>
<a class="btn" href="#" style="left:775px;top:355px;width:168px;height:37px">Contact Us Today</a>

<h2 class="abs serif intro-title">PLAYING THE PIANO</h2>
<div class="abs intro-copy">
  <p>When you think of a piano, you probably envision black and white keys but the piano is more than those harmonious sounds created by the player.</p>
  <p>The versatility and the musicianship instilled into the player from those keys is the true magic that comes from playing piano! Starting from the grassroots, experience different methods and styles of playing piano. To mark the milestones of progression, engage in one of Linden’s many unique performance opportunities like annual festival competitions, recitals or our examinations (Linden &amp; NPB).</p>
</div>
<a class="btn" href="#" style="left:145px;top:860px;width:139px;height:36px">Read More</a>
<div class="abs photo-girl" role="img" aria-label="Photograph of a young girl in a polka-dot top playing piano in a lesson"></div>

<div class="abs photo-back" role="img" aria-label="Photograph of hands on piano keys, dimmed"></div>
<div class="abs photo-front" role="img" aria-label="Photograph of a boy playing a white piano with his teacher beside him"></div>
<h2 class="abs serif section-title vision-title">OUR VISION</h2>
<div class="abs vision-copy">
  <p>Lorem ipsum dolor sit amet, consectetuer adipiscing elit, sed diam nonummy nibh euismod tincidunt ut laoreet dolore magna aliquam erat</p>
  <p>Lorem ipsum dolor sit amet, consectetuer adipiscing elit, sed diam nonummy nibh euismod tincidunt ut laoreet dolore magna aliquam erat volutpat. Ut wisi enim ad minim veniam, quis nostrud exerci tation ullamcorper suscipit lobortis nisl ut aliquip ex ea commodo consequat. Duis autem vel eum iriure dolor in hendrerit in vulputate velit esse molestie consequat, vel illum dolore eu feugiat nulla facilisis at vero eros et .</p>
</div>
<a class="btn" href="#" style="left:578px;top:1445px;width:168px;height:37px">Contact Us Today</a>

<div class="abs programs-band"></div>
<h2 class="abs serif section-title programs-title">OUR PROGRAMS</h2>
<div class="abs programs-sub">ALSO PROVIDE STUDENTS THE<br>OPPORTUNITY TO</div>
<div class="abs accent-right"></div>
<div class="abs photo-pianist" role="img" aria-label="Photograph of a smiling teenage girl seated at a black grand piano"></div>
<div class="abs accent-left"></div>
<div class="abs photo-hands" role="img" aria-label="Photograph of a child's hands on piano keys in warm sunlight"></div>
<ul class="abs programs-list">
  <li>Participate in large-scale performances.</li>
  <li>Perform at Linden’s many community events on a regular basis.</li>
  <li>Access the Lakeshore’s coolest Broadcast stage</li>
  <li>Attend Clinics, Masterclasses, and Jam Nights</li>
  <li>Access the Linden Rocks band program. Linden’s Band Program empowers and electrifies students to come together, create music and confidently hit the stage with their own band identity while having fun and honing their instrument.</li>
  <li>Register in our elite teaching program to learn how to pass on the magic and passion of playing the piano to students.</li>
</ul>
<a class="btn" href="#" style="left:603px;top:2397px;width:168px;height:36px">Contact Us Today</a>
<div class="abs keys-band" role="img" aria-label="Decorative band of light grey piano keys"></div>

<div class="abs quote-mark quote-open">“</div>
<p class="abs quote-text">Life is likea piano. What youget out of it depends on how you play it.</p>
<div class="abs quote-mark quote-close">”</div>
<div class="abs quote-rule"></div>
<div class="abs quote-notch"></div>
<div class="abs quote-name">MARTIN HALE</div>
<svg class="abs stars" width="74" height="13" viewBox="0 0 74 13" aria-label="Five star rating">
  <g fill="none" stroke="#f08a2c" stroke-width="0.9">
    <polygon points="6,1 7.5,4.6 11.3,4.8 8.3,7.2 9.3,11 6,8.8 2.7,11 3.7,7.2 0.7,4.8 4.5,4.6"/>
    <polygon transform="translate(15 0)" points="6,1 7.5,4.6 11.3,4.8 8.3,7.2 9.3,11 6,8.8 2.7,11 3.7,7.2 0.7,4.8 4.5,4.6"/>
    <polygon transform="translate(30 0)" points="6,1 7.5,4.6 11.3,4.8 8.3,7.2 9.3,11 6,8.8 2.7,11 3.7,7.2 0.7,4.8 4.5,4.6"/>
    <polygon transform="translate(45 0)" points="6,1 7.5,4.6 11.3,4.8 8.3,7.2 9.3,11 6,8.8 2.7,11 3.7,7.2 0.7,4.8 4.5,4.6"/>
    <polygon transform="translate(60 0)" points="6,1 7.5,4.6 11.3,4.8 8.3,7.2 9.3,11 6,8.8 2.7,11 3.7,7.2 0.7,4.8 4.5,4.6"/>
  </g>
</svg>

<section class="abs franchise">
  <h2>Franchise Opportunities</h2>
  <p>Be part of the linden academy family</p>
  <a class="btn" href="#" style="left:274px;top:129px;width:132px;height:36px">Know More</a>
</section>

<footer class="abs footer">
  <div class="foot-head" style="left:143px">QUICK LINKS</div>
  <ul class="quick-links">
    <li>Home</li><li>Piano Lessons</li><li>Franchising</li><li>Contact Us</li>
  </ul>
  <div class="foot-head" style="left:337px">CONTACT DETAILS</div>
  <div class="contact">
    <div class="row">
      <svg width="11" height="14" viewBox="0 0 11 14"><path d="M5.5 0A5 5 0 0 0 .5 5c0 3.8 5 9 5 9s5-5.2 5-9a5 5 0 0 0-5-5zm0 7A2 2 0 1 1 5.5 3a2 2 0 0 1 0 4z" fill="#fff"/></svg>
      <div><b style="font-size:11.5px">Chords by Linden</b><br>123 ipsum dolor sit amet,<br>consectetuer adipiscing.</div>
    </div>
    <div class="row">
      <svg width="12" height="12" viewBox="0 0 12 12"><path d="M2.4 0.6l2 2.2-1 1.4c.7 1.5 2 2.8 3.4 3.5l1.4-1 2.2 2-1 2.3C5 10.8 1 6.8.3 1.6z" fill="#fff"/></svg>
      <div>1-555-014-2290</div>
    </div>
    <div class="row">
      <svg width="12" height="10" viewBox="0 0 12 10"><rect x=".5" y=".5" width="11" height="9" fill="none" stroke="#fff"/><path d="M.5.5l5.5 5 5.5-5" fill="none" stroke="#fff"/></svg>
      <div>info@chordsbylinden.example</div>
    </div>
  </div>
  <div class="foot-head" style="left:621px">LOCATION MAP</div>
  <div class="map" role="img" aria-label="Location map of the studio area"></div>
  <div class="logo foot-logo"><span class="logo-dot"></span>CHORDS by Linden</div>
  <div class="socials" aria-label="Social media links"><span></span><span></span><span></span><span></span></div>
</footer>

<div class="abs copyright">Copyright © 2020 <b>Chords by Linden.</b> All Rights Reserved.</div>

</body>
</html>
```